Accountability Project Graphics

I want to create 10 social media graphics (new Instagram size 4:5 (1080 x 1350 pixels) focusing on our Quilvo Accountability App, using any of the 3 pictures attached. Use the attached pics only, NO RANDOM STOCK PHOTOGRAPHY. For the color scheme, use the landing page colors/fonts (attached).
You can add any of the 3 photos attached but I mainly need BOLD text that includes these headlines and sub-headlines on them.
Please NOTE for all the headlines below, also add this sub-headline on each graphic:
Stay Consistent with RT in Your Pocket!
Here are the headlines:
• Stop Starting Over Every Monday
• You don't need more willpower. You need more support
• Built for women who are tired of doing this alone
• When Motivation Fades, RT Checks In
• The Support System You've Been Missing
• Support When Motivation Disappears
• What if RT Checked in Every Day?
• The Missing Piece Isn't Another Diet
• Eat the food you love. Stay accountable every day.
• One Bad Meal Doesn't Mean You Failed
women over 40 trying to lose weight

```html
<!DOCTYPE html>
<html lang="en">
<head>
<meta charset="utf-8">
<title>Accountability App Social Graphics</title>
<link rel="stylesheet" href="https://fonts.googleapis.com/css2?family=DM+Serif+Display&family=Inter:wght@400;600;700&family=Caveat:wght@700&display=swap">
<style>
:root{
  --ink:#2b0f2c;
  --pink:#d52f68;
  --pink-deep:#b81f55;
  --bg-light:#fbe0e9;
  --bg-mid:#f6c9d8;
  --photo-dark:#241a22;
  --photo-mid:#4a3540;
  --white:#ffffff;
  --line:#e8a7bd;
}
*{box-sizing:border-box;margin:0;padding:0}
html,body{width:962px;height:1200px;overflow:hidden;background:#000}
.board{position:relative;width:962px;height:1200px;background:#000}
.tile{position:absolute;width:239px;height:298px;overflow:hidden;
  background:radial-gradient(circle at 75% 25%,var(--bg-mid) 0 28%,transparent 29%),linear-gradient(160deg,var(--bg-light),var(--bg-mid));
  font-family:"Inter",sans-serif;color:var(--ink)}
.c1{left:0}.c2{left:241px}.c3{left:482px}.c4{left:723px}
.r1{top:0}.r2{top:300px}.r3{top:600px}.r4{top:900px}
.photo{position:absolute;z-index:1;background:linear-gradient(180deg,var(--photo-mid),var(--photo-dark));border-radius:50px 50px 6px 6px}
.photo.soft{background:linear-gradient(180deg,#7a5a66,#2e3550)}
.snap{position:absolute;z-index:2;background:linear-gradient(160deg,#c97a95,#394066);border:3px solid var(--white);box-shadow:0 2px 5px rgba(0,0,0,.2)}
.headline{position:absolute;left:14px;font-family:"DM Serif Display",serif;font-size:20px;line-height:.92;color:var(--ink);z-index:2}
.headline .accent{color:var(--pink)}
.rule{position:absolute;height:1px;background:var(--pink);z-index:2}
.sub{position:absolute;left:14px;font-size:8px;font-weight:600;line-height:1.2;z-index:2}
.sub .accent{color:var(--pink)}
.tagline{position:absolute;left:14px;font-size:6px;font-weight:700;line-height:1.25;color:var(--pink);z-index:4}
.tagline.above-footer{bottom:32px}
.tagline.at-bottom{bottom:10px}
.list{position:absolute;left:18px;list-style:none;z-index:2}
.list li{display:flex;align-items:center;gap:6px;font-size:7.5px;font-weight:600;min-height:17px;line-height:1.15}
.list li::before{content:"";width:10px;height:10px;border-radius:50%;background:var(--pink);opacity:.85;flex:none}
.list .accent{color:var(--pink)}
.sticker{position:absolute;border-radius:50%;background:var(--pink);color:var(--white);font-family:"DM Serif Display",serif;font-size:10px;line-height:.95;display:flex;align-items:center;justify-content:center;text-align:center;border:3px solid var(--white);box-shadow:0 2px 6px rgba(0,0,0,.25);z-index:3}
.badge{position:absolute;border-radius:50%;background:var(--white);color:var(--pink);font-family:"Caveat",cursive;font-size:12px;line-height:.9;display:flex;align-items:center;justify-content:center;text-align:center;box-shadow:0 2px 5px rgba(0,0,0,.15);z-index:3}
.footer{position:absolute;left:0;right:0;bottom:0;height:28px;display:flex;justify-content:space-around;align-items:center;padding:0 6px;background:rgba(255,255,255,.25);border-top:1px solid var(--line);z-index:3}
.footer span{display:flex;align-items:center;gap:3px;font-size:4.6px;font-weight:600;line-height:1.1;width:52px}
.footer span::before{content:"";width:8px;height:8px;border:1px solid var(--pink);border-radius:50%;flex:none}
.phone{position:absolute;border-radius:16px;background:linear-gradient(180deg,#f3c6d6,#c8708f);border:4px solid #1c1c1e;z-index:2}
.phone .time{position:absolute;left:0;right:0;top:16px;text-align:center;color:var(--white);font-size:22px;font-weight:400}
.phone .date{position:absolute;left:0;right:0;top:44px;text-align:center;color:var(--white);font-size:5.5px}
.note{position:absolute;left:6px;right:6px;background:rgba(255,255,255,.9);border-radius:6px;padding:4px 5px;font-size:4.6px;line-height:1.3;color:var(--ink)}
.note b{font-size:5px}
.chat{position:absolute;left:36px;background:var(--white);border-radius:7px;padding:3px 6px;font-size:5.5px;line-height:1.3;box-shadow:0 1px 3px rgba(0,0,0,.1);z-index:2}
.chat b{color:var(--pink);font-weight:600}
.dot{position:absolute;left:14px;width:18px;height:18px;border-radius:50%;z-index:2}
.puzzle{position:absolute;background:var(--pink);color:var(--white);font-family:"DM Serif Display",serif;font-size:10px;line-height:1;text-align:center;display:flex;align-items:center;justify-content:center;border-radius:6px;transform:rotate(14deg);z-index:3}
.table{position:absolute;z-index:0;background:linear-gradient(180deg,#a8123f,#3a2630);border-radius:6px 0 0 0}
</style>
</head>
<body>
<main class="board">

<!-- 1 -->
<section class="tile c1 r1">
  <div class="photo" style="left:128px;top:16px;width:111px;height:254px" role="img" aria-label="Smiling coach in black lace top, hand on hip"></div>
  <div class="rule" style="left:16px;top:36px;width:74px"></div>
  <h2 class="headline" style="top:46px">Eat The<br>Food You<br>Love.<br><span class="accent">Stay<br>Accountable<br>Every Day.</span></h2>
  <div class="sub" style="top:176px;left:36px;font-size:5.5px">Meal help<br><span class="accent">that fits real life.</span></div>
  <div class="snap" style="left:12px;top:196px;width:70px;height:50px;transform:rotate(-5deg)" role="img" aria-label="Two women hugging"></div>
  <div class="snap" style="left:78px;top:168px;width:54px;height:68px;transform:rotate(3deg)" role="img" aria-label="Two women laughing together"></div>
  <p class="tagline above-footer">Stay Consistent with<br>RT in Your Pocket!</p>
  <div class="footer"><span>Daily Accountability</span><span>Meal Help &amp; Recipes</span><span>Text Support</span><span>Motivation for Real Life</span></div>
</section>

<!-- 2 -->
<section class="tile c2 r1">
  <div class="photo" style="left:140px;top:14px;width:99px;height:284px" role="img" aria-label="Smiling coach in black lace top"></div>
  <h2 class="headline" style="top:52px;left:17px;font-size:21px">The<br>Support<br>System<br>You’ve<br><span class="accent">Been<br>Missing.</span></h2>
  <ul class="list" style="top:184px"><li>Weekly Calls</li><li>Text Support</li><li>Delicious Recipes</li><li>Encouragement</li><li>Accountability</li></ul>
  <div class="sticker" style="left:170px;top:204px;width:56px;height:56px">We’ve<br>got your<br>back!</div>
  <p class="tagline at-bottom" style="left:18px">Stay Consistent with<br>RT in Your Pocket!</p>
</section>

<!-- 3 -->
<section class="tile c3 r1">
  <div class="photo soft" style="left:106px;top:34px;width:133px;height:232px" role="img" aria-label="Two women laughing side by side"></div>
  <h2 class="headline" style="top:66px;font-size:20px">Built For<br>Women<br>Who Are<br>Tired Of<br><span class="accent">Doing<br>This Alone.</span></h2>
  <div class="sub" style="top:200px">Real support<br>for <span class="accent">real life.</span></div>
  <p class="tagline above-footer">Stay Consistent with<br>RT in Your Pocket!</p>
  <div class="footer"><span>Daily Accountability</span><span>Meal Help &amp; Recipes</span><span>Text Support</span><span>Motivation for Real Life</span></div>
</section>

<!-- 4 -->
<section class="tile c4 r1">
  <div class="photo" style="left:80px;top:164px;width:54px;height:134px" role="img" aria-label="Smiling coach in black top"></div>
  <div class="phone" style="left:126px;top:30px;width:100px;height:226px;transform:rotate(5deg)">
    <div class="time">9:30</div><div class="date">Monday, May 12</div>
    <div class="note" style="top:152px"><b>RT in Your Pocket</b><br>RT — Good morning, sis! Let’s make today count!</div>
  </div>
  <h2 class="headline" style="top:52px;font-size:21px">What If<br>RT Checked<br>In<br><span class="accent">Every Day?</span></h2>
  <div class="sub" style="top:163px;font-size:7px">Your coach, motivator,<br>and accountability<br>partner —<br><span class="accent">right in your pocket.</span></div>
  <p class="tagline" style="top:216px">Stay Consistent<br>with RT in<br>Your Pocket!</p>
</section>

<!-- 5 -->
<section class="tile c1 r2">
  <div class="photo" style="left:130px;top:20px;width:109px;height:278px" role="img" aria-label="Smiling coach in black lace top"></div>
  <h2 class="headline" style="top:58px;font-size:26px">One Bad<br>Meal<br>Doesn’t<br>Mean<br><span class="accent">You Failed.</span></h2>
  <div class="sub" style="top:192px;font-size:10px">RT helps you<br><span class="accent">reset</span>, not quit.</div>
  <div class="badge" style="left:90px;top:206px;width:50px;height:50px">You’ve<br>got this,<br>sis!</div>
  <p class="tagline at-bottom">Stay Consistent with<br>RT in Your Pocket!</p>
</section>

<!-- 6 -->
<section class="tile c2 r2">
  <div class="photo soft" style="left:120px;top:40px;width:119px;height:220px" role="img" aria-label="Two women hugging and laughing"></div>
  <h2 class="headline" style="top:46px;font-size:20px">You Don’t<br>Need More<br>Willpower.<br><span class="accent">You Need<br>More<br>Support.</span></h2>
  <ul class="list" style="top:178px"><li>Daily Check-Ins</li><li>Meal Help &amp; Recipes</li><li>Motivation That Sticks</li></ul>
  <p class="tagline above-footer">Stay Consistent with<br>RT in Your Pocket!</p>
  <div class="footer"><span>Daily Accountability</span><span>Meal Help &amp; Recipes</span><span>Text Support</span><span>Motivation for Real Life</span></div>
</section>

<!-- 7 -->
<section class="tile c3 r2">
  <div class="photo soft" style="left:100px;top:30px;width:139px;height:268px" role="img" aria-label="Two women laughing side by side"></div>
  <h2 class="headline" style="top:52px;left:17px;font-size:20px">The<br>Support<br>System<br>You’ve<br><span class="accent">Been<br>Missing.</span></h2>
  <ul class="list" style="top:172px"><li>Weekly Calls</li><li>Text Support</li><li>Delicious Recipes</li><li>Encouragement</li><li>Accountability</li></ul>
  <div class="sticker" style="left:170px;top:204px;width:56px;height:56px">We’ve<br>got your<br>back!</div>
  <p class="tagline at-bottom" style="left:18px">Stay Consistent with<br>RT in Your Pocket!</p>
</section>

<!-- 8 -->
<section class="tile c4 r2">
  <div class="phone" style="left:122px;top:22px;width:112px;height:244px">
    <div class="time" style="font-size:24px">8:00</div><div class="date">Monday, May 12</div>
    <div class="note" style="top:62px"><b>RT</b><br>Good morning, sis! Let’s make today count!</div>
  </div>
  <div class="photo" style="left:30px;top:146px;width:92px;height:98px" role="img" aria-label="Smiling coach in black top"></div>
  <h2 class="headline" style="top:44px;left:10px;font-size:20px">What If RT<br>Checked In<br><span class="accent">Every Day?</span></h2>
  <div class="sub" style="top:120px;left:10px;font-size:6.8px">Your coach, motivator,<br>and accountability partner<br>— right in your pocket.</div>
  <p class="tagline above-footer" style="left:10px">Stay Consistent with<br>RT in Your Pocket!</p>
  <div class="footer"><span>Daily Accountability</span><span>Meal Help &amp; Recipes</span><span>Text Support</span><span>Motivation for Real Life</span></div>
</section>

<!-- 9 -->
<section class="tile c1 r3">
  <div class="photo" style="left:122px;top:18px;width:117px;height:252px" role="img" aria-label="Smiling coach in black lace top"></div>
  <h2 class="headline" style="top:58px;font-size:26px">Stop<br>Starting<br>Over<br><span class="accent">Every<br>Monday</span></h2>
  <div class="rule" style="left:16px;top:186px;width:92px"></div>
  <div class="sub" style="top:194px;font-size:8.5px">Let RT help you<br><span class="accent">stay accountable</span><br>all week.</div>
  <p class="tagline above-footer">Stay Consistent with<br>RT in Your Pocket!</p>
  <div class="footer"><span>Daily Accountability</span><span>Meal Help &amp; Recipes</span><span>Text Support</span><span>Motivation for Real Life</span></div>
</section>

<!-- 10 -->
<section class="tile c2 r3">
  <div class="photo" style="left:140px;top:14px;width:99px;height:256px" role="img" aria-label="Smiling coach in black lace top"></div>
  <div class="rule" style="left:12px;top:31px;width:74px"></div>
  <h2 class="headline" style="top:44px;left:10px;font-size:21px">Eat The<br>Food You<br>Love.<br><span class="accent">Stay<br>Accountable<br>Every Day.</span></h2>
  <div class="sub" style="top:180px;left:34px;font-size:5.5px">Meal help<br><span class="accent">that fits real life.</span></div>
  <div class="snap" style="left:10px;top:198px;width:72px;height:50px;transform:rotate(-5deg)" role="img" aria-label="Two women hugging"></div>
  <div class="snap" style="left:80px;top:172px;width:54px;height:68px;transform:rotate(3deg)" role="img" aria-label="Two women laughing together"></div>
  <p class="tagline above-footer" style="left:10px">Stay Consistent with<br>RT in Your Pocket!</p>
  <div class="footer"><span>Daily Accountability</span><span>Meal Help &amp; Recipes</span><span>Text Support</span><span>Motivation for Real Life</span></div>
</section>

<!-- 11 -->
<section class="tile c3 r3">
  <div class="table" style="left:90px;top:186px;width:149px;height:84px" role="img" aria-label="Pool table edge"></div>
  <div class="photo" style="left:124px;top:16px;width:115px;height:254px" role="img" aria-label="Smiling coach in black lace top"></div>
  <h2 class="headline" style="top:54px">The<br>Missing<br>Piece Isn’t<br><span class="accent">Another Diet.</span></h2>
  <div class="sub" style="top:144px;font-size:8.5px">It’s support that<br><span class="accent">stays with you.</span></div>
  <div class="puzzle" style="left:26px;top:184px;width:74px;height:50px">Support<br>Changes<br>Everything</div>
  <p class="tagline above-footer">Stay Consistent with<br>RT in Your Pocket!</p>
  <div class="footer"><span>Daily Accountability</span><span>Meal Help &amp; Recipes</span><span>Text Support</span><span>Motivation for Real Life</span></div>
</section>

<!-- 12 -->
<section class="tile c4 r3">
  <div class="photo" style="left:128px;top:18px;width:111px;height:252px" role="img" aria-label="Smiling coach in black lace top"></div>
  <h2 class="headline" style="top:52px;font-size:22px">When<br>Motivation<br>Fades,<br><span class="accent">RT Checks In.</span></h2>
  <div class="sub" style="top:158px;font-size:8px">Accountability<br>that keeps you<br><span class="accent">moving.</span></div>
  <div class="dot" style="top:190px;background:var(--photo-mid)" role="img" aria-label="Coach avatar"></div>
  <div class="chat" style="top:191px"><b>RT:</b> Hey sis!<br>How are you today?</div>
  <div class="dot" style="top:218px;background:var(--pink)"></div>
  <div class="chat" style="top:218px"><b>You:</b> I needed this!<br>Thanks RT!</div>
  <p class="tagline above-footer">Stay Consistent with<br>RT in Your Pocket!</p>
  <div class="footer"><span>Daily Accountability</span><span>Meal Help &amp; Recipes</span><span>Text Support</span><span>Motivation for Real Life</span></div>
</section>

<!-- 13 -->
<section class="tile c1 r4">
  <div class="table" style="left:96px;top:168px;width:143px;height:130px" role="img" aria-label="Pool table edge"></div>
  <div class="photo" style="left:124px;top:24px;width:115px;height:274px" role="img" aria-label="Smiling coach in black lace top"></div>
  <h2 class="headline" style="top:48px;left:13px;font-size:22px">Support<br>When<br>Motivation<br><span class="accent">Disappears.</span></h2>
  <div class="sub" style="top:148px;left:15px;font-size:7.5px">Because<br><span class="accent">consistency</span><br>needs backup.</div>
  <ul class="list" style="top:182px;left:15px">
    <li><span>We <span class="accent">Listen</span></span></li>
    <li><span>We <span class="accent">Coach</span></span></li>
    <li><span>We <span class="accent">Support</span></span></li>
    <li><span>We <span class="accent">Celebrate</span><br>Your Wins</span></li>
  </ul>
  <p class="tagline at-bottom" style="left:15px">Stay Consistent with<br>RT in Your Pocket!</p>
</section>

</main>
</body>
</html>
```